Modern Verdell Tree Care Website

I need a website for a full service Tree Care company. The company provides tree pruning, tree removal, tree preservation, emergency services, stump grinding, and emergency tree services.

Target Market(s)

Customers that need tree services

Industry/Entity Type

Landscaping, Tree Services

Coding

Coded - Design and coding required

Number of Pages Required

5+ page

Font styles to use
Sans Serif

Requirements
Must have
• Good clean design that showcases the services the company provides.
Nice to have
• Services page; contact form, blog, home page, about page

```html
<!DOCTYPE html>
<html lang="en">
<head>
<meta charset="utf-8">
<title>Verdell Tree Care</title>
<link href="https://fonts.googleapis.com/css2?family=Poppins:wght@400;500;600;700&display=swap" rel="stylesheet">
<style>
:root{
  --green:#7cc242;
  --green-dark:#4f8a24;
  --orange:#f9a834;
  --ink:#5b6770;
  --text:#222;
  --muted:#8a8f94;
  --cream:#f4f4e3;
  --black:#0d0d0d;
  --white:#fff;
}
*{box-sizing:border-box;margin:0;padding:0}
html,body{width:1200px;height:4983px;overflow:hidden}
body{font-family:'Poppins',sans-serif;color:var(--text);background:var(--white);position:relative}
.abs{position:absolute}
section,header,footer{position:absolute;left:0;width:1200px}
.btn{position:absolute;display:flex;align-items:center;justify-content:center;color:#fff;font-weight:600;text-transform:uppercase;letter-spacing:.5px}
.tree-mark{position:absolute;width:40px;height:54px}
.section-title{position:absolute;left:0;width:1200px;text-align:center;font-size:38px;font-weight:700;color:var(--ink);letter-spacing:.5px}

/* header */
.site-header{top:0;height:130px;background:#fff}
.brand{position:absolute;left:44px;top:20px;display:flex;align-items:center;gap:10px;font-weight:700;font-size:30px;color:var(--green);line-height:1}
.brand .sq{width:40px;height:40px;background:var(--green)}
.call{position:absolute;top:20px;display:flex;align-items:center;gap:14px}
.call .ico{width:50px;height:50px;border-radius:50%;background:var(--green);display:flex;align-items:center;justify-content:center}
.call small{display:block;font-size:12px;color:#444}
.call strong{display:block;font-size:22px;font-weight:500;color:#111;line-height:1.1}
.main-nav{position:absolute;left:44px;top:93px;width:871px;height:73px;background:var(--green);z-index:3}
.main-nav a{position:absolute;top:0;height:73px;line-height:73px;color:#fff;font-size:18px;text-decoration:none;transform:translateX(-50%)}
.main-nav i{position:absolute;top:18px;width:2px;height:37px;background:#fff}
.quote-btn{left:915px;top:93px;width:243px;height:73px;background:var(--orange);font-size:22px;z-index:3}

/* hero */
.hero{top:130px;height:780px;background:linear-gradient(180deg,#223019 0%,#2e3f20 45%,#3b3325 75%,#2b3a1e 100%)}
.hero h1{position:absolute;top:236px;width:1200px;text-align:center;color:#fff;font-size:60px;font-weight:700;line-height:70px}
.hero h1 em{font-style:normal;color:var(--orange)}
.hero p{position:absolute;top:406px;width:1200px;text-align:center;color:#fff;font-size:22px;letter-spacing:.5px}
.hero .btn{top:472px;height:52px;border-radius:26px;font-size:19px}
.grass{position:absolute;left:0;width:1200px;height:24px;background:var(--green)}

/* about */
.about{top:910px;height:773px}
.ring{position:absolute;border:3px dashed var(--green);border-radius:50%}
.photo{position:absolute;border-radius:50%}
.about h2{position:absolute;left:598px;top:262px;font-size:36px;font-weight:700;color:var(--ink)}
.about p{position:absolute;left:600px;top:330px;width:560px;font-size:13.5px;line-height:22.5px;color:var(--muted)}
.about .btn{left:598px;top:478px;width:209px;height:48px;border-radius:24px;background:var(--orange);font-size:18px}

/* services */
.services{top:1683px;height:780px;background:var(--cream)}
.svc-card{position:absolute;top:246px;width:240px;height:344px;background:linear-gradient(135deg,#fff 58%,#f1f1f1 58%);text-align:center}
.svc-card .ring{left:62px;top:22px;width:116px;height:116px;border-width:2px}
.svc-card .photo{left:71px;top:31px;width:98px;height:98px}
.svc-card h3{position:absolute;top:192px;width:100%;font-size:17px;font-weight:600}
.svc-card p{position:absolute;top:224px;left:18px;width:204px;font-size:13px;line-height:22px;color:var(--muted)}
.svc-card .go{position:absolute;left:97px;top:321px;width:46px;height:46px;border-radius:50%;background:var(--orange);display:flex;align-items:center;justify-content:center}
.services .view{left:490px;top:684px;width:207px;height:47px;background:var(--orange);font-size:19px}

/* why */
.why{top:2463px;height:662px}
.why .sub{position:absolute;top:208px;left:380px;width:440px;text-align:center;font-size:14px;line-height:22px;color:var(--muted)}
.feature{position:absolute;display:flex;align-items:center;gap:18px}
.feature svg{width:78px;height:78px;flex:none}
.feature span{font-size:18px;font-weight:500;line-height:22px;color:#333}

/* testimonials */
.reviews{top:3125px;height:558px;background:var(--cream)}
.review{position:absolute;top:236px;width:430px;height:225px;background:linear-gradient(160deg,#fff 50%,#f2f2f2 50%);box-shadow:0 4px 16px rgba(0,0,0,.06)}
.review .stars{position:absolute;left:28px;top:30px;display:flex;gap:6px}
.review .qbadge{position:absolute;right:25px;top:22px;width:76px;height:76px;border-radius:50%;background:#fff;display:flex;align-items:center;justify-content:center;box-shadow:0 2px 8px rgba(0,0,0,.06)}
.review h4{position:absolute;left:28px;top:92px;font-size:12px;font-weight:600;text-transform:uppercase}
.review p{position:absolute;left:20px;top:136px;width:390px;font-size:12.5px;line-height:22px;color:var(--muted)}

/* articles */
.articles{top:3683px;height:825px}
.post{position:absolute;top:265px;width:290px;height:416px;background:#fff;box-shadow:0 6px 22px rgba(0,0,0,.08)}
.post .img{position:absolute;left:0;top:0;width:290px;height:226px}
.post .date{position:absolute;left:22px;top:185px;width:54px;height:54px;background:var(--green);color:#fff;text-align:center;font-weight:600;font-size:18px;line-height:24px;padding-top:6px}
.post .date small{display:block;font-size:10px;line-height:10px}
.post .meta{position:absolute;left:24px;top:256px;font-size:10.5px;color:#999;display:flex;gap:22px}
.post h3{position:absolute;left:24px;top:283px;width:250px;font-size:18px;line-height:23px;font-weight:500;color:var(--green-dark)}
.post .more{position:absolute;left:24px;top:366px;width:114px;height:34px;background:#f1f1ea;font-size:10px;font-weight:600;display:flex;align-items:center;justify-content:center;color:#333}

/* footer */
.site-footer{top:4508px;height:475px;background:var(--black);color:#fff}
.site-footer .brand{left:58px;top:118px;font-size:26px}
.site-footer .brand .sq{width:32px;height:32px}
.f-about{position:absolute;left:58px;top:180px;width:230px;font-size:14px;line-height:19px}
.socials{position:absolute;left:58px;top:270px;display:flex;gap:30px}
.socials span{width:16px;height:16px;border-radius:50%;background:var(--green)}
.f-head{position:absolute;top:112px;font-size:19px;font-weight:600;color:var(--orange)}
.f-links{position:absolute;left:416px;top:162px;list-style:none}
.f-links li{font-size:15px;height:40.5px}
.thumb{position:absolute;width:74px;height:56px;background:linear-gradient(135deg,#5f7f3a,#2f4a1e)}
.f-contact{position:absolute;left:896px;top:172px;list-style:none}
.f-contact li{display:flex;align-items:center;gap:18px;height:61.5px;font-size:15px}
.f-bottom{position:absolute;left:0;top:405px;width:1200px;border-top:1px solid #333}
.f-bottom span{position:absolute;top:26px;font-size:10.5px}
</style>
</head>
<body>

<header class="site-header">
  <div class="brand"><span class="sq"></span>Verdell Tree Care</div>
  <div class="call" style="left:507px">
    <span class="ico"><svg width="24" height="24" viewBox="0 0 24 24"><path fill="#fff" d="M6.6 10.8a15.1 15.1 0 0 0 6.6 6.6l2.2-2.2c.3-.3.7-.4 1-.2 1.1.4 2.3.6 3.6.6.6 0 1 .4 1 1V20c0 .6-.4 1-1 1C10.6 21 3 13.4 3 4c0-.6.4-1 1-1h3.5c.6 0 1 .4 1 1 0 1.3.2 2.5.6 3.6.1.3 0 .7-.2 1z"/></svg></span>
    <div><small>CALL NOW</small><strong>(555) 214 0187</strong></div>
  </div>
  <div class="call" style="left:845px">
    <span class="ico"><svg width="24" height="24" viewBox="0 0 24 24"><path fill="#fff" d="M6.6 10.8a15.1 15.1 0 0 0 6.6 6.6l2.2-2.2c.3-.3.7-.4 1-.2 1.1.4 2.3.6 3.6.6.6 0 1 .4 1 1V20c0 .6-.4 1-1 1C10.6 21 3 13.4 3 4c0-.6.4-1 1-1h3.5c.6 0 1 .4 1 1 0 1.3.2 2.5.6 3.6.1.3 0 .7-.2 1z"/></svg></span>
    <div><small>CALL NOW</small><strong>(555) 318 4420</strong></div>
  </div>
  <nav class="main-nav">
    <a style="left:68px">HOME</a><i style="left:134px"></i>
    <a style="left:219px">ABOUT</a><i style="left:298px"></i>
    <a style="left:389px">SERVICES</a><i style="left:475px"></i>
    <a style="left:562px">BLOG</a><i style="left:631px"></i>
    <a style="left:732px">CONTACT</a>
  </nav>
  <a class="btn quote-btn">Get a Quote</a>
</header>

<section class="hero" role="img" aria-label="Photo of a house surrounded by tall trees and a lawn">
  <h1>Call <em>Verdell</em> for All Your<br>Tree Care Needs</h1>
  <p>SERVING LAFAYETTE AND SURROUNDING AREAS</p>
  <a class="btn" style="left:372px;width:222px;background:var(--orange)">Our Services</a>
  <a class="btn" style="left:606px;width:218px;background:var(--green)">Get a Quote</a>
  <div class="grass" style="top:756px"></div>
</section>

<section class="about">
  <div class="ring" style="left:20px;top:106px;width:514px;height:514px"></div>
  <div class="photo" role="img" aria-label="Arborist trimming a green hedge" style="left:46px;top:133px;width:464px;height:464px;background:linear-gradient(135deg,#2f5a1f,#4e7d2c 60%,#6b5a3a)"></div>
  <div class="photo" role="img" aria-label="Close-up of hedge shears cutting leaves" style="left:266px;top:394px;width:276px;height:276px;border:8px solid #fff;background:linear-gradient(135deg,#3d6b26,#28461a)"></div>
  <svg class="tree-mark" style="left:592px;top:185px" viewBox="0 0 40 54"><path d="M20 2 L38 38 H2 Z" fill="var(--green)"/><rect x="18" y="38" width="4" height="14" fill="#b9803e"/></svg>
  <h2>WHO WE ARE</h2>
  <p>Lorem ipsum dolor sit amet, consectetur adipiscing elit, sed do eiusmod tempor incididunt ut labore et dolore magna aliqua. Quis ipsum suspendisse ultrices gravida. Risus commodo viverra. Lorem ipsum dolor sit amet, consectetur adipiscing elit, sed do eiusmod tempor incididunt ut labore et dolore magna aliqua.</p>
  <a class="btn">More About Us</a>
</section>

<section class="services">
  <svg class="tree-mark" style="left:556px;top:50px" viewBox="0 0 40 54"><path d="M20 2 L38 38 H2 Z" fill="var(--green)"/><rect x="18" y="38" width="4" height="14" fill="#b9803e"/></svg>
  <h2 class="section-title" style="top:116px">OUR SERVICES</h2>

  <article class="svc-card" style="left:74px">
    <div class="ring"></div><div class="photo" role="img" aria-label="Hedge trimmer at work" style="background:linear-gradient(135deg,#3f6d28,#2a4a1b)"></div>
    <h3>Tree Trimming</h3><p>Lorem ipsum dolor sit amet consectetur adipiscing,Quis ipsum suspendisse</p>
    <span class="go"><svg width="18" height="18" viewBox="0 0 18 18"><path d="M3 7h7V3l6 6-6 6v-4H3z" fill="#fff"/></svg></span>
  </article>
  <article class="svc-card" style="left:348px">
    <div class="ring"></div><div class="photo" role="img" aria-label="Worker cutting a branch" style="background:linear-gradient(135deg,#35592a,#6a4a36)"></div>
    <h3>Tree Removal</h3><p>Lorem ipsum dolor sit amet consectetur adipiscing,Quis ipsum suspendisse</p>
    <span class="go"><svg width="18" height="18" viewBox="0 0 18 18"><path d="M3 7h7V3l6 6-6 6v-4H3z" fill="#fff"/></svg></span>
  </article>
  <article class="svc-card" style="left:623px">
    <div class="ring"></div><div class="photo" role="img" aria-label="Shears pruning leaves" style="background:linear-gradient(135deg,#3d6b26,#223d16)"></div>
    <h3>Tree Pruning</h3><p>Lorem ipsum dolor sit amet consectetur adipiscing,Quis ipsum suspendisse</p>
    <span class="go"><svg width="18" height="18" viewBox="0 0 18 18"><path d="M3 7h7V3l6 6-6 6v-4H3z" fill="#fff"/></svg></span>
  </article>
  <article class="svc-card" style="left:900px">
    <div class="ring"></div><div class="photo" role="img" aria-label="Fallen tree after a storm" style="background:linear-gradient(180deg,#a9b8a0,#4d6b35)"></div>
    <h3>Storm Damage</h3><p>Lorem ipsum dolor sit amet consectetur adipiscing,Quis ipsum suspendisse</p>
    <span class="go"><svg width="18" height="18" viewBox="0 0 18 18"><path d="M3 7h7V3l6 6-6 6v-4H3z" fill="#fff"/></svg></span>
  </article>

  <a class="btn view">View All</a>
</section>

<section class="why">
  <svg class="tree-mark" style="left:563px;top:85px" viewBox="0 0 40 54"><path d="M20 2 L38 38 H2 Z" fill="var(--green)"/><rect x="18" y="38" width="4" height="14" fill="#b9803e"/></svg>
  <h2 class="section-title" style="top:152px">WHY CHOOSE US</h2>
  <p class="sub">Lorem ipsum dolor sit amet consectetur adipiscing,Quis ipsum suspendisse</p>

  <div class="feature" style="left:152px;top:343px">
    <svg viewBox="0 0 78 78" fill="none" stroke="var(--green)" stroke-width="2.5"><rect x="10" y="8" width="44" height="60" rx="3"/><path d="M19 22h26M19 32h26M19 42h16"/><circle cx="56" cy="52" r="10"/></svg>
    <span>Licensed and<br>Insured</span>
  </div>
  <div class="feature" style="left:505px;top:343px">
    <svg viewBox="0 0 78 78" fill="none" stroke="var(--green)" stroke-width="2.5"><circle cx="39" cy="39" r="30"/><path d="M39 18v21l12 8"/></svg>
    <span>24 Hours<br>Emergency Services</span>
  </div>
  <div class="feature" style="left:834px;top:343px">
    <svg viewBox="0 0 78 78" fill="none" stroke="var(--green)" stroke-width="2.5"><rect x="8" y="44" width="26" height="20" rx="3"/><path d="M34 50 L68 16 L72 20 L38 58"/></svg>
    <span>Locally Owned<br>and Oprated</span>
  </div>
  <div class="feature" style="left:148px;top:496px">
    <svg viewBox="0 0 78 78" fill="none" stroke="var(--green)" stroke-width="2.5"><path d="M39 6 L66 16 V38 C66 56 52 66 39 72 C26 66 12 56 12 38 V16 Z"/><path d="M27 39 l9 9 l16 -18"/></svg>
    <span>Safety is our<br>First Priority</span>
  </div>
  <div class="feature" style="left:505px;top:496px">
    <svg viewBox="0 0 78 78" fill="none" stroke="var(--green)" stroke-width="2.5"><rect x="10" y="8" width="40" height="60" rx="3"/><path d="M18 22h24M18 32h24M18 42h14"/><rect x="44" y="40" width="24" height="30" rx="2"/><path d="M49 48h14M49 56h14M49 63h14"/></svg>
    <span>Free<br>Estimates</span>
  </div>
  <div class="feature" style="left:840px;top:496px">
    <svg viewBox="0 0 78 78" fill="none" stroke="var(--green)" stroke-width="2.5"><circle cx="39" cy="22" r="8"/><circle cx="18" cy="34" r="6"/><circle cx="60" cy="34" r="6"/><path d="M25 60 C25 42 53 42 53 60M6 62 C6 48 26 48 28 54M72 62 C72 48 52 48 50 54"/></svg>
    <span>Professional<br>Work</span>
  </div>
</section>

<section class="reviews">
  <svg class="tree-mark" style="left:546px;top:48px" viewBox="0 0 40 54"><path d="M20 2 L38 38 H2 Z" fill="var(--green)"/><rect x="18" y="38" width="4" height="14" fill="#b9803e"/></svg>
  <h2 class="section-title" style="top:116px">HAPPY CUSTOMERS</h2>

  <article class="review" style="left:137px">
    <div class="stars">
      <svg width="26" height="26" viewBox="0 0 24 24"><path d="M12 2l3 7h7l-5.6 4.3 2.1 7.2L12 16.3 5.5 20.5l2.1-7.2L2 9h7z" fill="var(--green)"/></svg>
      <svg width="26" height="26" viewBox="0 0 24 24"><path d="M12 2l3 7h7l-5.6 4.3 2.1 7.2L12 16.3 5.5 20.5l2.1-7.2L2 9h7z" fill="var(--green)"/></svg>
      <svg width="26" height="26" viewBox="0 0 24 24"><path d="M12 2l3 7h7l-5.6 4.3 2.1 7.2L12 16.3 5.5 20.5l2.1-7.2L2 9h7z" fill="var(--green)"/></svg>
      <svg width="26" height="26" viewBox="0 0 24 24"><path d="M12 2l3 7h7l-5.6 4.3 2.1 7.2L12 16.3 5.5 20.5l2.1-7.2L2 9h7z" fill="var(--green)"/></svg>
      <svg width="26" height="26" viewBox="0 0 24 24"><path d="M12 2l3 7h7l-5.6 4.3 2.1 7.2L12 16.3 5.5 20.5l2.1-7.2L2 9h7z" fill="var(--green)"/></svg>
    </div>
    <span class="qbadge"><svg width="42" height="34" viewBox="0 0 42 34"><path d="M4 32c0-16 4-26 14-30v6c-5 3-6 8-6 12h6v12zM24 32c0-16 4-26 14-30v6c-5 3-6 8-6 12h6v12z" fill="var(--orange)"/></svg></span>
    <h4>Dana Whitlow</h4>
    <p>There are many variations of passages of Lorem Ipsum available, but the majority have suffered alteration in some form, by injected humour, randomised words .</p>
  </article>
  <article class="review" style="left:642px">
    <div class="stars">
      <svg width="26" height="26" viewBox="0 0 24 24"><path d="M12 2l3 7h7l-5.6 4.3 2.1 7.2L12 16.3 5.5 20.5l2.1-7.2L2 9h7z" fill="var(--green)"/></svg>
      <svg width="26" height="26" viewBox="0 0 24 24"><path d="M12 2l3 7h7l-5.6 4.3 2.1 7.2L12 16.3 5.5 20.5l2.1-7.2L2 9h7z" fill="var(--green)"/></svg>
      <svg width="26" height="26" viewBox="0 0 24 24"><path d="M12 2l3 7h7l-5.6 4.3 2.1 7.2L12 16.3 5.5 20.5l2.1-7.2L2 9h7z" fill="var(--green)"/></svg>
      <svg width="26" height="26" viewBox="0 0 24 24"><path d="M12 2l3 7h7l-5.6 4.3 2.1 7.2L12 16.3 5.5 20.5l2.1-7.2L2 9h7z" fill="var(--green)"/></svg>
      <svg width="26" height="26" viewBox="0 0 24 24"><path d="M12 2l3 7h7l-5.6 4.3 2.1 7.2L12 16.3 5.5 20.5l2.1-7.2L2 9h7z" fill="var(--green)"/></svg>
    </div>
    <span class="qbadge"><svg width="42" height="34" viewBox="0 0 42 34"><path d="M4 32c0-16 4-26 14-30v6c-5 3-6 8-6 12h6v12zM24 32c0-16 4-26 14-30v6c-5 3-6 8-6 12h6v12z" fill="var(--orange)"/></svg></span>
    <h4>Dana Whitlow</h4>
    <p>There are many variations of passages of Lorem Ipsum available, but the majority have suffered alteration in some form, by injected humour, randomised words .</p>
  </article>
</section>

<section class="articles">
  <svg class="tree-mark" style="left:558px;top:70px" viewBox="0 0 40 54"><path d="M20 2 L38 38 H2 Z" fill="var(--green)"/><rect x="18" y="38" width="4" height="14" fill="#b9803e"/></svg>
  <h2 class="section-title" style="top:138px">OUR LATEST ARTICLES</h2>

  <article class="post" style="left:122px">
    <div class="img" role="img" aria-label="Seedling pots and a garden trowel on a wooden table" style="background:linear-gradient(135deg,#7a5a3c,#c79a62 55%,#5d7a3a)"></div>
    <div class="date">27<small>Feb</small></div>
    <div class="meta"><span>&#9679; ArborDesk</span><span>&#9632; 2 Comments</span></div>
    <h3>Vegetable crops that do not need pollinators</h3>
    <span class="more">READ MORE &rarr;</span>
  </article>
  <article class="post" style="left:435px">
    <div class="img" role="img" aria-label="Hands holding a bowl of fresh cherry tomatoes" style="background:linear-gradient(135deg,#5e7d3a,#b7452f 50%,#4b6a2e)"></div>
    <div class="date">27<small>Feb</small></div>
    <div class="meta"><span>&#9679; ArborDesk</span><span>&#9632; 2 Comments</span></div>
    <h3>Grow your own pumpkins even in small spaces</h3>
    <span class="more">READ MORE &rarr;</span>
  </article>
  <article class="post" style="left:747px">
    <div class="img" role="img" aria-label="Freshly pulled carrots held above the soil" style="background:linear-gradient(135deg,#6c8a3d,#c06a2c 55%,#3d4e6b)"></div>
    <div class="date">27<small>Feb</small></div>
    <div class="meta"><span>&#9679; ArborDesk</span><span>&#9632; 2 Comments</span></div>
    <h3>In our gardens plants for the shade garden</h3>
    <span class="more">READ MORE &rarr;</span>
  </article>

  <div class="grass" style="top:787px;height:38px"></div>
</section>

<footer class="site-footer">
  <div class="brand"><span class="sq"></span>Verdell Tree Care</div>
  <p class="f-about">Call Verdell for All Your Tree Care NeedsServing Lafayette and Sorrounding Areas</p>
  <div class="socials"><span></span><span></span><span></span></div>

  <h4 class="f-head" style="left:416px">LINKS</h4>
  <ul class="f-links"><li>Home</li><li>About</li><li>Services</li><li>Blog</li><li>Contact</li></ul>

  <h4 class="f-head" style="left:600px">GALLERY</h4>
  <div class="thumb" role="img" aria-label="Tree work photo" style="left:600px;top:162px"></div>
  <div class="thumb" role="img" aria-label="Tree work photo" style="left:682px;top:162px"></div>
  <div class="thumb" role="img" aria-label="Tree work photo" style="left:600px;top:229px"></div>
  <div class="thumb" role="img" aria-label="Tree work photo" style="left:682px;top:229px"></div>

  <h4 class="f-head" style="left:896px">CONTACT</h4>
  <ul class="f-contact">
    <li><svg width="22" height="22" viewBox="0 0 24 24"><path fill="var(--green)" d="M6.6 10.8a15.1 15.1 0 0 0 6.6 6.6l2.2-2.2c.3-.3.7-.4 1-.2 1.1.4 2.3.6 3.6.6.6 0 1 .4 1 1V20c0 .6-.4 1-1 1C10.6 21 3 13.4 3 4c0-.6.4-1 1-1h3.5c.6 0 1 .4 1 1 0 1.3.2 2.5.6 3.6.1.3 0 .7-.2 1z"/></svg>(555) 214 0187</li>
    <li><svg width="22" height="22" viewBox="0 0 24 24"><path fill="var(--green)" d="M6.6 10.8a15.1 15.1 0 0 0 6.6 6.6l2.2-2.2c.3-.3.7-.4 1-.2 1.1.4 2.3.6 3.6.6.6 0 1 .4 1 1V20c0 .6-.4 1-1 1C10.6 21 3 13.4 3 4c0-.6.4-1 1-1h3.5c.6 0 1 .4 1 1 0 1.3.2 2.5.6 3.6.1.3 0 .7-.2 1z"/></svg>(555) 318 4420</li>
    <li><svg width="22" height="24" viewBox="0 0 24 24"><path fill="var(--green)" d="M12 2a7 7 0 0 0-7 7c0 5 7 13 7 13s7-8 7-13a7 7 0 0 0-7-7zm0 9.5A2.5 2.5 0 1 1 12 6.5a2.5 2.5 0 0 1 0 5z"/></svg>18 Cedar Hollow Rd, Lafayette</li>
  </ul>

  <div class="f-bottom">
    <span style="left:62px">Copyright &copy; 2024 Verdell Tree Care. All Rights Reserved</span>
    <span style="left:927px">Privacy Policy | Terms and Conditions</span>
  </div>
</footer>

</body>
</html>
```